Dentistry Office

We want a new design for a Dentist's office website.

The theme is: "We provide high quality, state-of-the-art, dental care in a comfortable, caring environment."

The site currently has a menu on the left of the page with about 40 items on it. There is a great deal of textual content on each page, plus several illustrations.

We want to do this using CSS, so we need specifications in the CSS for all possible elements. The CSS needs to be named in a logical manner for easy use.

Every dentist on the planet seems to use lots of Flash. We don't want to because it is so distracting. We are looking for an elegant solution targeting 24-55 age group, but not excluding anyone.

The following (from another dentist's site) can give you a taste of what we want to communicate on the site:

"After 20 years of teaching dentists how to refine their technique and many years of writing textbooks, I currently devote my time to my office and the hands-on practice of dentistry. I'd like to welcome you personally to my dental practice, and I invite you to meet my highly experienced team of professionals.

"We have offered complete dental care of the highest quality since 1978. We provide Preventive Services, Tooth Whitening and Cosmetic Dentistry for a beautiful smile, Endodontics (root canal treatment) to treat painful teeth, Sedation Dentistry so you can relax, and Dental Implants to restore what is missing. We offer total care.

"Our approach to your health is simple: We use our education, experience and dedication to provide every patient with superior dental care.

"This passion for excellence is not just a goal, but a standard every member of our team holds.

"We also pride ourselves with our state of the art procedures, training and technology. This includes creating a beautiful smile using techniques that preserve as much of the original tooth as possible.

"Our abilities are renowned throughout the dental profession and I hope if you have any questions you will contact us by an e-mail note, by phone or just by dropping by."

Keep in mind the screen shape and dimensions. Your design needs to work in the normal screen proportions, regardless of how it looks when you post it here. Scrolling is OK, but the first impression needs to work.
Updates

Keep in mind that there will be about 250 words, or more, on each page.

Competitors web sites:

http://www.brindlecovedentist.example/

http://www.brindlecovedentalcare.example/

http://www.grinsbymarlowvaledental.example/

http://www.tenbyfamilydentalcare.example/

http://www.quelmardental.example/

http://www.dovrinadental.example/

We need to compete with these.

Target Market(s)

Generally adults seeking the most experienced and comfortable-to-be-with dentist.

Industry/Entity Type

Training

Requirements
Must have
• Must stand apart from other dentists.
• Must be elegant.
• Must have a horizontal menu structure across all columns, NOT a vertical that requires scrolling, no popout, pop down, etc. menus.
• We are looking for something special.
• Do not waste your time or ours putting up templates and things you have used before.
• Personally, I do not see how someone outside the US can understand the northern California dental market. But you are welcome to try.
Should not have
• Flash or graphics that move
• The look of a template
• Folksy fonts
• Looks like you used it 20 times before

```html
<!DOCTYPE html>
<html lang="en">
<head>
<meta charset="utf-8">
<title>Tobias Wrenfield, DDS, FAGD – Brindle Cove Dentist</title>
<link rel="stylesheet" href="https://fonts.googleapis.com/css2?family=Tinos:ital,wght@0,400;0,700;1,400;1,700&family=Arimo:wght@400;700&display=swap">
<style>
:root{
  --ink:#222;
  --navy:#1f3a52;
  --nav-bg:#111;
  --nav-edge:#3a3a3a;
  --hero-a:#5f7f9c;
  --hero-b:#a9bfd2;
  --hero-c:#d7e2ec;
  --panel:#dde4ec;
  --panel-line:#b9c5d2;
  --paper:#fff;
  --foot:#c3cbd1;
  --frame:#8a8f94;
  --link-green:#2c8a3c;
  --link-teal:#3b8c95;
}
*{box-sizing:border-box;margin:0;padding:0}
html,body{width:753px;height:1200px;overflow:hidden;background:var(--paper)}
body{font-family:"Arimo",Arial,sans-serif;color:var(--ink);font-size:8.4px;line-height:1.3}
.site-header{height:64px;background:linear-gradient(#fff,#e9ecef);position:relative;border-bottom:1px solid #ccc}
.brand{position:absolute;left:26px;top:14px;font-family:"Tinos",serif}
.brand-name{font-size:25px;color:var(--ink);line-height:1}
.brand-name span{color:var(--navy)}
.brand-sub{font-size:13px;text-align:right;margin-top:3px}
.header-contact{position:absolute;right:14px;top:8px;font-family:"Tinos",serif;font-size:9.5px;line-height:1.25}
.main-nav{height:27px;background:linear-gradient(#2b2b2b,var(--nav-bg));display:flex;align-items:center;justify-content:space-around;padding:0 20px;border-bottom:2px solid #000}
.main-nav a{color:#fff;text-decoration:none;font-family:"Tinos",serif;font-size:11px}
.main-nav i{color:#888;font-style:normal}
.hero{height:189px;position:relative;background:linear-gradient(100deg,var(--hero-a),var(--hero-b) 55%,var(--hero-c));overflow:hidden}
.hero-text{position:absolute;left:37px;top:36px;width:410px;color:#fff;font-family:"Tinos",serif;font-size:17px;line-height:1.3}
.hero-photo{position:absolute;right:0;top:0;width:210px;height:189px;background:radial-gradient(circle at 60% 40%,#f1d8c4,#c9d6e2 70%)}
.services{margin:6px 0 0;height:146px;background:var(--panel);display:flex;padding:6px 0 0 27px;gap:0}
.service-col{width:160px}
.service-col:nth-child(1){width:144px}
.service-col h3{font-family:"Tinos",serif;font-weight:400;font-size:12.5px;color:#111;border-bottom:1px solid var(--panel-line);width:90%;margin-bottom:3px;padding-bottom:1px}
.service-col ul{list-style:none}
.service-col li{font-size:8.6px;line-height:1.38;color:#333}
.service-col li::before{content:"› ";color:#555;font-weight:700}
.content{display:flex;padding:12px 27px 0;height:594px}
.article{width:505px}
.article h1{font-family:"Tinos",serif;font-weight:400;font-size:17px;color:var(--navy);border-bottom:1px solid #ccc;padding-bottom:3px;margin-bottom:10px}
.article h2{font-family:"Tinos",serif;font-weight:400;font-size:12px;margin:9px 0 5px}
.article p{margin-bottom:7px}
.article a{color:#000;font-weight:700}
.sidebar{margin-left:25px;width:159px}
.office-photo{height:80px;border-radius:8px;background:linear-gradient(#6f5a3e,#a2773e 45%,#5a3d2a);border:2px solid #bbb}
.card{border:1px solid var(--frame);border-radius:8px;margin-top:21px;padding:6px 8px;text-align:center}
.card h4{font-family:"Arimo",sans-serif;font-weight:400;font-size:11.5px;margin-bottom:5px}
.map{height:222px;background:linear-gradient(#f4f4f4,#e6e6e6);border:1px solid #aaa}
.card .more{display:block;margin-top:6px;font-size:8px;color:#000}
.hours{text-align:left}
.hours h4{text-align:center;font-family:"Tinos",serif;font-size:13px}
.hours p{margin-bottom:3px}
.hours li{list-style:none;font-style:italic;font-weight:700;font-size:9px;line-height:1.4}
.site-footer{height:173px;background:linear-gradient(#e4e8eb,var(--foot) 40%);position:relative}
.copy{position:absolute;left:27px;top:45px;font-weight:700;font-size:8.6px}
.copy p{margin-bottom:12px}
.links{position:absolute;left:407px;top:40px;width:320px;height:113px;background:#fff;border:1px solid var(--frame);border-radius:8px;padding:6px 10px}
.links h5{font-weight:400;font-size:9px;margin-bottom:6px}
.link-cols{display:flex;gap:12px}
.link-col{width:92px;font-size:7.6px;line-height:1.25}
.org{font-family:"Arimo",sans-serif;font-weight:700;font-size:10px;height:24px;display:flex;align-items:center;gap:4px;margin-bottom:3px}
.org.green{color:var(--link-green)}
.org.grey{color:#777}
.org.teal{color:var(--link-teal)}
.dot{width:9px;height:9px;background:currentColor;display:inline-block;flex:none}
</style>
</head>
<body>
<header class="site-header">
  <div class="brand">
    <div class="brand-name">Tobias Wrenfield, <span>DDS, FAGD</span></div>
    <div class="brand-sub">Brindle Cove Dentist</div>
  </div>
  <address class="header-contact" style="font-style:normal">Tobias Wrenfield, DDS, FAGD<br>2240 Halden Ave. Ste C<br>Brindle Cove, CA 95012<br>555-014-2271</address>
</header>
<nav class="main-nav">
  <a href="#">Home</a><i>|</i><a href="#">Why We Are Different?</a><i>|</i><a href="#">Technologies We Offer</a><i>|</i><a href="#">Meet Dr. Wrenfield</a><i>|</i><a href="#">Our Staff</a><i>|</i><a href="#">Contact Us / Links</a>
</nav>
<section class="hero">
  <p class="hero-text">Brindle Cove Dentist - Tobias Wrenfield, DDS, Providing Cosmetic Dentistry Excellence to Patients in Brindle Cove, Halden County and the Marrow Bay Area.</p>
  <div class="hero-photo" role="img" aria-label="Smiling patient holding a pink flower"></div>
</section>
<section class="services">
  <div class="service-col"><h3>Education</h3><ul><li>Emergency Dental Care</li><li>Your Mouth</li><li>Your Tooth</li><li>Cracked Tooth?</li><li>Missing a Tooth?</li><li>Sensitive Teeth</li><li>Dry Mouth</li><li>Tooth Grinding</li><li>Sleep Dentistry</li><li>Videos</li></ul></div>
  <div class="service-col"><h3>Preventative</h3><ul><li>What is Preventive Care?</li><li>Taking Care of Your Teeth</li><li>Eating Right</li><li>Dental Check-Ups</li><li>Sealants</li><li>Periodontal Disease</li><li>Kicking the Habit</li><li>Night Guards</li><li>Dental X-Rays</li><li>Antibiotics with Treatment</li></ul></div>
  <div class="service-col"><h3>Cosmetics</h3><ul><li>Cosmetic Dentistry</li><li>Bleaching and Whitening</li><li>Cosmetic Bonding</li><li>Esthetic Veneers</li><li>Tooth Shaping</li></ul></div>
  <div class="service-col"><h3>Restorations</h3><ul><li>Crowns/Caps: Each Step</li><li>CMBRs</li><li>Porcelain Bridges</li><li>Bonded Dental Bridges</li><li>Gold Restorations</li><li>Implants</li><li>Treating Cracked Teeth</li><li>Periodontal (gum) Treatment</li></ul></div>
  <div class="service-col"><h3>Visiting our office</h3><ul><li>Where to Stay</li><li>First Visit / Map</li><li>Financial Policy</li><li>Dental Insurance</li></ul></div>
</section>
<main class="content">
  <article class="article">
    <h1>Why we are different?</h1>
    <h2>Excellence:</h2>
    <p>I have over 32 years experience as a dental practitioner, dental author, and educator. We have a continuing commitment to care for our patients by combining the best technical ability, best materials, with artistic creativity. We treat one patient at a time and every procedure is done until it is as good as it can be. No compromises.</p>
    <h2>Dignity:</h2>
    <p>We respect each person as an individual. We treat all patients as we would for members of our own families, with compassion and integrity.</p>
    <h2>Service:</h2>
    <p>We are here to create radiant smiles, optimum health, and seek to provide service that makes every patient feel well taken care of.</p>
    <h2>Comfort:</h2>
    <p>We are all very concerned about your comfort and offer a number of choices in sedation and sleep dentistry to ensure your will have a favorable experience. In addition, we offer the widest selection of conservative treatment options to shorten your dental treatment time.</p>
    <h2>Enjoyment:</h2>
    <p>We love what we do and work to establish long-term quality relationships with our patients and staff at our office. Our office is state of the art, clean and comfortable. We do research, teach and continually take courses from the best educators in the world to stay abreast of the latest technologies.</p>
    <h2>Our Office Philosophy</h2>
    <p>Dental care is a complex and intricate science. Few patients fully understand the nature of this profession. Dentists do not sell fillings, veneers or crowns. They provide a service. The only real thing a dentist has to sell is his or her time, skill, and judgment and that varies considerably among practitioners.</p>
    <p>Dentistry is a demanding and rapidly changing profession that takes many years to learn and the good part of a lifetime to master. It involves a sophisticated understanding of biological, chemical, and physical sciences. Artistic abilities are also essential in providing esthetic and natural appearing restorations.</p>
    <p>Our policy is to provide you with the highest quality health care humanly possible. We have spent an unusually large amount of time learning the finest techniques. We are dedicated to doing whatever is necessary to be as current as possible in this high tech field. In providing dental care we take no short cuts and use the absolute highest quality materials and technical support.</p>
    <h2>About Dr. Wrenfield</h2>
    <p>Dr. Wrenfield is a world authority on tooth colored restorations and esthetic dentistry. He has authored a number of textbooks for dentists, consults for the profession, and is an active teacher in the profession. Click here to view <a href="#">Dr. Wrenfield's CV</a>.</p>
  </article>
  <aside class="sidebar">
    <div class="office-photo" role="img" aria-label="Office waiting room with chairs"></div>
    <div class="card">
      <h4>Brindle Cove Map:</h4>
      <div class="map" role="img" aria-label="Street map showing the office location"></div>
      <a class="more" href="#">Click for Large View</a>
    </div>
    <div class="card hours">
      <h4>Office Timing</h4>
      <p>Our usual office hours are:</p>
      <ul>
        <li>Monday 9 am to 6 pm</li>
        <li>Tuesday 9 am to 5 pm</li>
        <li>Wednesday 9 am to 5 pm</li>
        <li>Thursday 9 am to 5 pm</li>
        <li>Friday 7:30 am to 5 pm</li>
      </ul>
    </div>
  </aside>
</main>
<footer class="site-footer">
  <div class="copy">
    <p>Copyright © 2010 wrenfielddental.example. All Rights Reserved.</p>
    <div>Office Phone: (555) 014-2271<br>Office Fax: (555) 014-2290<br>email Dr. Wrenfield at: office@wrenfielddental.example</div>
  </div>
  <div class="links">
    <h5>Dental Links:</h5>
    <div class="link-cols">
      <div class="link-col"><div class="org green"><span class="dot"></span>Orvan Dental</div>Emergency Dental Help<br>Oral Health Videos<br>Oral Health Topics<br>Dental Minute News</div>
      <div class="link-col"><div class="org grey"><span class="dot"></span>Keel Institute</div>Dental Emergencies<br>Dental Health<br>Dental Insurance<br>Kids Corner<br>Dental Terminology</div>
      <div class="link-col"><div class="org teal"><span class="dot"></span>Northvale DS</div>Course Outlines<br>Upcoming Courses<br>Web Links<br>Dr Wrenfield CV<br>Keel Store</div>
    </div>
  </div>
</footer>
</body>
</html>
```